FinTech company looking to revamp and expand client-facing interface for our financial models

Pellworth Engines currently has a very simple website that allows clients to interact with our financial models. We are looking to completely redesign the current site and add several extra pages to provide extra functionality. We want the design to have a modern, slick feel, that will work on both a desktop or a tablet. It should be straightforward for clients to move between different pages at any time, and clear from the layout how to interact with the more advanced features. We have included screenshots of existing pages in the attached design brief, as well as sketches of the functionality required by the new pages, but can't provide a direct link to the current site.
Target Market(s)
Professional investors that will be paying to access the interface
Industry/Entity Type
Finance
Number of Pages Required
4 page
Colors
Designer to choose colors to be used in the design.
Look and feel
Each slider illustrates characteristics of the customer's brand and the style your logo design should communicate.

```html
<!DOCTYPE html>
<html lang="en">
<head>
<meta charset="utf-8">
<title>QORVEX — Backtest</title>
<link href="https://fonts.googleapis.com/css2?family=Open+Sans:wght@400;600;700&family=Roboto+Condensed:wght@400&family=Roboto:wght@400;500&display=swap" rel="stylesheet">
<style>
:root{
  --page:#e9e9e9;
  --surface:#f2f2f2;
  --white:#ffffff;
  --navy:#0b2e63;
  --teal:#06675f;
  --dark:#333333;
  --darker:#2c2c2c;
  --black:#1b1b1b;
  --row-alt:#efefef;
  --text:#111111;
  --grid:#dcdcdc;
  --line:#8fb7b3;
}
*{box-sizing:border-box;margin:0;padding:0}
html,body{width:1169px;height:1200px;overflow:hidden;background:var(--page)}
.stage{position:relative;width:1300px;height:1335px;transform:scale(0.9);transform-origin:0 0;font-family:"Open Sans",sans-serif;color:var(--text)}
.frame{position:absolute;left:15px;top:15px;width:1270px;height:1305px;background:var(--surface)}
.topnav{position:absolute;left:15px;top:15px;width:1270px;height:60px;background:var(--white);display:flex;box-shadow:0 4px 10px rgba(0,0,0,.06)}
.topnav .brand{width:180px;display:flex;align-items:center;justify-content:center;font-weight:700;font-size:18px;border-right:1px solid #e6e6e6}
.topnav .range{width:90px;display:flex;align-items:center;justify-content:center;font-weight:700;font-size:14px;border-right:1px solid #e6e6e6}
.topnav .spacer{flex:1;border-right:1px solid #e6e6e6}
.topnav .link{display:flex;align-items:center;gap:8px;padding:0 24px;font-weight:700;font-size:13px;border-right:1px solid #e6e6e6}
.topnav .link:last-child{border-right:none;padding-right:56px}
.page-title{position:absolute;left:487px;top:115px;width:325px;height:55px;background:var(--navy);color:#fff;font-size:21px;font-weight:600;display:flex;align-items:center;justify-content:center;border-radius:3px;letter-spacing:.3px}
.chart-card{position:absolute;left:460px;top:190px;width:805px;height:450px;background:var(--white);box-shadow:0 2px 8px rgba(0,0,0,.08)}
.chart-card svg{position:absolute;left:0;top:0}
.control-panel{position:absolute;left:15px;top:190px;width:445px;height:570px;background:var(--dark)}
.control-panel .inner{position:absolute;left:90px;top:0;width:355px;height:450px;background:var(--darker)}
.modes{position:absolute;left:52px;top:270px;display:flex;gap:10px}
.mode{width:181px;height:45px;display:flex;align-items:center;justify-content:center;color:#fff;font-size:17px;font-weight:600;border:2px solid #fff;border-bottom:none;border-radius:4px 4px 0 0}
.mode.active{background:var(--navy)}
.form-label{position:absolute;color:#fff;font-weight:700;font-size:17px}
.field{position:absolute;height:30px;background:#fff;border-radius:3px;font-size:15px;padding-left:13px;display:flex;align-items:center}
.select-btn{position:absolute;left:317px;top:344px;width:106px;height:32px;background:var(--teal);color:#fff;border:1px solid #fff;border-radius:3px;font-weight:700;font-size:15px;display:flex;align-items:center;justify-content:center}
.run-btn{position:absolute;left:159px;top:619px;width:157px;height:52px;background:var(--navy);color:#fff;border:2px solid #fff;border-radius:4px;font-weight:700;font-size:16px;display:flex;align-items:center;justify-content:center}
.model-tab{position:absolute;left:460px;top:350px;width:50px;height:250px;background:var(--dark);border-radius:0 4px 4px 0}
.model-tab span{position:absolute;left:8px;top:205px;transform:rotate(-90deg);transform-origin:0 0;color:#fff;font-weight:600;font-size:17px;letter-spacing:.5px;white-space:nowrap}
.model-tab svg{position:absolute;left:36px;top:112px}
.data-table{position:absolute;top:690px;border-collapse:collapse;box-shadow:0 2px 8px rgba(0,0,0,.08);font-family:"Roboto Condensed",sans-serif;font-size:17px;text-align:center}
.data-table th{height:70px;background:var(--black);color:#fff;font-family:"Open Sans",sans-serif;font-weight:600;font-size:17px;border-left:1px solid #333}
.data-table th:first-child{border-left:none}
.data-table td{height:69px;background:var(--white);border-left:1px solid #f0f0f0}
.data-table tr:nth-child(even) td{background:var(--row-alt)}
.stats{left:105px;width:400px}
.stats th{color:#3a3a3a}
.stats td{width:200px}
.trades{left:545px;width:720px}
.trades td,.trades th{width:180px}
.load-more{position:absolute;top:1200px;width:200px;height:40px;background:var(--teal);color:#fff;border-radius:3px;display:flex;align-items:center;justify-content:center;gap:12px;font-weight:700;font-size:14px}
</style>
</head>
<body>
<div class="stage">
  <div class="frame"></div>

  <nav class="topnav">
    <div class="brand">QORVEX</div>
    <div class="range">250D</div>
    <div class="range">83D</div>
    <div class="range">42D</div>
    <div class="spacer"></div>
    <div class="link">
      <svg width="24" height="24" viewBox="0 0 24 24" fill="none" stroke="#111" stroke-width="2"><path d="M3 11 12 3l9 8"/><path d="M5 10v11h5v-6h4v6h5V10"/><path d="M16 5V3h2v4"/></svg>MODELS</div>
    <div class="link">
      <svg width="24" height="24" viewBox="0 0 24 24" fill="none" stroke="#111" stroke-width="1.6"><circle cx="12" cy="12" r="4"/><circle cx="12" cy="12" r="8" stroke-dasharray="2 2"/><circle cx="12" cy="12" r="11" stroke-dasharray="1.5 3"/></svg>SENSITIVITIES</div>
    <div class="link">
      <svg width="24" height="24" viewBox="0 0 24 24" fill="none" stroke="#111" stroke-width="1.8"><path d="M12 2l3 6.5 7 .8-5.2 4.8 1.4 7L12 17.5 5.8 21l1.4-7L2 9.3l7-.8z"/></svg>FAVOURITES</div>
  </nav>

  <div class="page-title">BACKTEST PAGE</div>

  <div class="chart-card">
    <svg width="805" height="450" viewBox="460 190 805 450" font-family="Roboto, sans-serif" font-size="13" fill="#222">
      <g stroke="var(--grid)" stroke-width="1">
        <line x1="505" y1="293" x2="1197" y2="293"/>
        <line x1="505" y1="370" x2="1197" y2="370"/>
        <line x1="505" y1="448" x2="1197" y2="448"/>
        <line x1="505" y1="525" x2="1197" y2="525"/>
        <line x1="510" y1="268" x2="510" y2="556"/>
        <line x1="594" y1="268" x2="594" y2="556"/>
        <line x1="682" y1="268" x2="682" y2="556"/>
        <line x1="770" y1="268" x2="770" y2="556"/>
        <line x1="850" y1="268" x2="850" y2="556"/>
        <line x1="937" y1="268" x2="937" y2="556"/>
        <line x1="1022" y1="268" x2="1022" y2="556"/>
        <line x1="1109" y1="268" x2="1109" y2="556"/>
        <line x1="1175" y1="268" x2="1175" y2="556"/>
      </g>
      <line x1="505" y1="556" x2="1197" y2="556" stroke="#bbb"/>
      <g text-anchor="middle">
        <text x="506" y="263">Nov 2018</text><text x="591" y="263">Dec 2018</text><text x="678" y="263">Jan 2019</text><text x="766" y="263">Feb 2019</text><text x="845" y="263">Mar 2019</text><text x="933" y="263">Apr 2019</text><text x="1018" y="263">May 2019</text><text x="1105" y="263">Jun 2019</text><text x="1176" y="263">Jul 2019</text>
        <text x="509" y="575">Nov 2018</text><text x="594" y="575">Dec 2018</text><text x="682" y="575">Jan 2019</text><text x="770" y="575">Feb 2019</text><text x="849" y="575">Mar 2019</text><text x="937" y="575">Apr 2019</text><text x="1022" y="575">May 2019</text><text x="1109" y="575">Jun 2019</text><text x="1176" y="575">Jul 2019</text>
      </g>
      <polyline fill="none" stroke="var(--line)" stroke-width="1.6" points="510,445 520,440 530,440 540,437 545,480 555,475 565,478 580,478 585,455 590,460 595,478 600,470 605,460 625,460 628,445 640,440 648,400 665,397 672,410 680,415 688,405 690,385 700,390 705,375 720,373 725,367 740,365 748,345 752,350 758,335 762,355 767,385 770,370 775,375 780,390 785,370 790,375 795,370 800,365 805,390 810,375 818,378 822,345 827,345 832,355 840,345 850,350 860,345 865,318 875,310 885,305 895,310 897,355 905,345 915,340 930,345 938,315 942,340 950,340 960,345 965,370 975,372 980,340 990,335 1000,340 1005,330 1015,340 1020,345 1025,330 1040,325 1045,340 1060,335 1080,340 1085,335 1090,340 1100,325 1105,340 1115,325 1122,320 1132,325 1145,330 1155,325 1160,305 1170,300 1178,298 1185,303 1190,300 1197,290"/>
    </svg>
  </div>

  <section class="control-panel"><div class="inner"></div></section>
  <div class="modes">
    <div class="mode active">Mode 1</div>
    <div class="mode">Mode 2</div>
  </div>
  <div class="form-label" style="left:55px;top:350px">Model:</div>
  <div class="field" style="left:127px;top:344px;width:181px;height:32px">Model name</div>
  <div class="select-btn">Select</div>
  <div class="form-label" style="left:183px;top:430px">Parameters:</div>
  <div class="form-label" style="left:55px;top:471px">Entry:</div>
  <div class="field" style="left:152px;top:465px;width:271px">0.5</div>
  <div class="form-label" style="left:55px;top:516px">Exit:</div>
  <div class="field" style="left:152px;top:510px;width:271px">-0.3</div>
  <div class="form-label" style="left:55px;top:561px">Lookback:</div>
  <div class="field" style="left:152px;top:555px;width:271px">5</div>
  <div class="run-btn">RUN</div>

  <div class="model-tab">
    <span>SELECT A MODEL</span>
    <svg width="28" height="28" viewBox="0 0 28 28"><circle cx="14" cy="14" r="12.5" fill="var(--navy)" stroke="#fff" stroke-width="2"/><path d="M20 14H9M13 9.5 8.5 14 13 18.5" fill="none" stroke="#fff" stroke-width="2.2"/></svg>
  </div>

  <table class="data-table stats">
    <tr><th colspan="2">Stats</th></tr>
    <tr><td>Stat 1</td><td>0.5</td></tr>
    <tr><td>Stat 2</td><td>-3</td></tr>
    <tr><td>Stat 3</td><td>30%</td></tr>
    <tr><td>Stat 4</td><td>0.5</td></tr>
    <tr><td>Stat 5</td><td>-3</td></tr>
    <tr><td>Stat 6</td><td>30%</td></tr>
  </table>

  <table class="data-table trades">
    <tr><th>Open</th><th>Close</th><th>Size</th><th>Return</th></tr>
    <tr><td>2018-04-05</td><td>2018-04-07</td><td>13</td><td>5%</td></tr>
    <tr><td>2018-04-05</td><td>2018-04-07</td><td>12</td><td>7%</td></tr>
    <tr><td>2018-04-05</td><td>2018-04-07</td><td>15</td><td>6%</td></tr>
    <tr><td>2018-04-05</td><td>2018-04-07</td><td>16</td><td>9%</td></tr>
    <tr><td>2018-04-05</td><td>2018-04-07</td><td>12</td><td>8%</td></tr>
    <tr><td>2018-04-05</td><td>2018-04-07</td><td>19</td><td>6%</td></tr>
  </table>

  <div class="load-more" style="left:205px">
    <svg width="22" height="22" viewBox="0 0 22 22" fill="none" stroke="#fff" stroke-width="2"><path d="M11 2v12M6 9l5 5 5-5M2 15v5h18v-5"/></svg>LOAD MORE</div>
  <div class="load-more" style="left:805px">
    <svg width="22" height="22" viewBox="0 0 22 22" fill="none" stroke="#fff" stroke-width="2"><path d="M11 2v12M6 9l5 5 5-5M2 15v5h18v-5"/></svg>LOAD MORE</div>
</div>
</body>
</html>
```